Easy Marinade Labels for Butchery Store

Need a set of labels designed for a Butchery Shop. They will sit in the top left corner of the packets as a triangle (7cm each side). Easy because the only major requirement is the label name and some small text saying "Please ask in store to see spec sheet for ingredients". Extra points for finding a fun way to incorporate the logo and/or images of food (garlic bulbs, chilli, spices ect) to enhance the label. List of Marinade Names below: GarlicPepper Mint & RosemarySatayBBQChilli Plum & GingerSundried Tomato & BasilBuffaloHoney SoyHoi-SinPer PeriSpicy CajunTeriyakiBlack Bean Ive also attached the logo and an example of how the label might sit on a packet of meat. Thanks

Target Market(s)

Butchery Deli Shop Customers

Industry/Entity Type

Food Store

Font styles to use
Serif
Sans Serif
Decorative
Other font styles liked:
• Fun font that isn't a generic Quellbrix Font?

Colors

Designer to choose colors to be used in the design.

Requirements
Must have
• Product Name
• Small text saying "Please ask in store to see spec sheet for ingredients"
Nice to have
• Photos of ingredients that would match that type of marinade - Chilli, Garlic, Spices.
• Fenly Oak Logo - not essential if it doesn't look good on the label / doesn't fit.

```html
<!DOCTYPE html>
<html lang="en">
<head>
<meta charset="utf-8">
<title>Marinade Label – Wild Garlic Crumble</title>
<link rel="stylesheet" href="https://fonts.googleapis.com/css2?family=Amatic+SC:wght@700&family=Open+Sans:wght@800&display=swap">
<style>
  :root {
    --page: #ffffff;
    --frame-yellow: #f2e51d;
    --garlic-light: #e9e1dc;
    --garlic-mid: #cdbfb8;
    --garlic-cream: #eadfb6;
    --garlic-dark: #8f7f76;
    --ink-white: #ffffff;
    --ink-shadow: #111111;
  }
  html, body {
    margin: 0;
    padding: 0;
    width: 1200px;
    height: 900px;
    overflow: hidden;
    background: var(--page);
  }
  .label-canvas {
    display: block;
    width: 1200px;
    height: 900px;
  }
  .label-intro {
    font-family: "Open Sans", sans-serif;
    font-weight: 800;
    font-size: 15px;
    fill: var(--ink-white);
    filter: drop-shadow(1px 1px 0 var(--ink-shadow));
  }
  .label-name {
    font-family: "Amatic SC", cursive;
    font-weight: 700;
    fill: var(--ink-white);
    stroke: var(--ink-white);
    stroke-width: 1.5px;
    filter: drop-shadow(-3px 3px 0 var(--ink-shadow));
  }
  .label-name--top { font-size: 80px; }
  .label-name--bottom { font-size: 100px; }
  .label-note {
    font-family: "Open Sans", sans-serif;
    font-weight: 800;
    font-size: 26px;
    fill: var(--ink-white);
  }
</style>
</head>
<body>
<svg class="label-canvas" viewBox="0 0 1200 900" xmlns="http://www.w3.org/2000/svg">
  <defs>
    <linearGradient id="garlicTones" x1="0" y1="0" x2="1" y2="1">
      <stop offset="0" stop-color="var(--garlic-mid)"/>
      <stop offset="0.35" stop-color="var(--garlic-light)"/>
      <stop offset="0.6" stop-color="var(--garlic-cream)"/>
      <stop offset="1" stop-color="var(--garlic-mid)"/>
    </linearGradient>
    <linearGradient id="baseShade" x1="0" y1="0" x2="0" y2="1">
      <stop offset="0" stop-color="var(--garlic-dark)" stop-opacity="0"/>
      <stop offset="1" stop-color="var(--garlic-dark)" stop-opacity="0.85"/>
    </linearGradient>
  </defs>

  <g class="label-triangle">
    <polygon class="label-photo" role="img" aria-label="Photo of whole garlic bulbs and peeled cloves"
             points="621,177 150,643 1092,643" fill="url(#garlicTones)"/>
    <polygon class="label-shade" points="230,565 1014,565 1092,643 150,643" fill="url(#baseShade)"/>
    <polygon class="label-frame" points="621,174 146,646 1096,646"
             fill="none" stroke="var(--frame-yellow)" stroke-width="7" stroke-linejoin="miter"/>
  </g>

  <text class="label-intro" x="620" y="375" text-anchor="middle" textLength="171" lengthAdjust="spacingAndGlyphs">MARINATED WITH</text>
  <text class="label-name label-name--top" x="617" y="450" text-anchor="middle" textLength="296" lengthAdjust="spacingAndGlyphs">WILD GARLIC</text>
  <text class="label-name label-name--bottom" x="620" y="540" text-anchor="middle" textLength="298" lengthAdjust="spacingAndGlyphs">CRUMBLE</text>
  <text class="label-note" x="621" y="622" text-anchor="middle" textLength="740" lengthAdjust="spacingAndGlyphs">PLEASE ASK IN STORE TO SEE SPEC SHEET FOR INGREDIENTS</text>
</svg>
</body>
</html>
```